Executive Business Card for Healthcare Company [Need Today]

I need a business card design for a healthcare company. The only branding the company has thus far is a logo. The cards will be utilized by company executives. The design I envision will be vibrant and appealing but with a corporate feel. They shouldn't be too casual or playful. I would like to complete this project TODAY if possible.

Target Market(s)

Healthcare vendors, other executives in healthcare and pharmaceuticals

Industry/Entity Type

Pharmaceutical

Contact Information for Business Card

See attachment

Font styles to use
Serif
Sans Serif

Colors

Designer to choose colors to be used in the design.

```html
<!DOCTYPE html>
<html lang="en">
<head>
<meta charset="utf-8">
<title>Corvia Therapeutics – Executive Business Cards</title>
<link href="https://fonts.googleapis.com/css2?family=Roboto:wght@300;400&display=swap" rel="stylesheet">
<style>
  :root{
    --backdrop:#cccccc;
    --card:#fafafa;
    --teal:#1aaebb;
    --green:#46b58e;
    --divider:#6b6b6b;
    --ink:#555555;
    --muted:#777777;
    --white:#ffffff;
  }
  html,body{margin:0;padding:0;overflow:hidden}
  body{width:1200px;height:586px;background:var(--backdrop);position:relative;font-family:'Roboto',sans-serif}
  .card{position:absolute;width:286px;height:172px;border-radius:10px;overflow:hidden;background:var(--card)}
  .card--front{background:linear-gradient(180deg,var(--teal),var(--green))}
  .front-name{position:absolute;left:0;right:0;top:62px;text-align:center;color:var(--white);font-weight:300;font-size:26px;letter-spacing:.5px}
  .front-address{position:absolute;left:0;right:0;top:156px;text-align:center;color:rgba(255,255,255,.85);font-size:7.5px;font-weight:300}
  .stripe{position:absolute;left:0;top:0;bottom:0;width:25px;background:linear-gradient(180deg,var(--teal),var(--green))}
  .stripe::after{content:"";position:absolute;right:-3px;top:0;bottom:0;width:3px;background:var(--divider)}
  .brand{position:absolute;left:42px;top:18px;display:flex;align-items:center;gap:8px}
  .brand-dot{width:47px;height:47px;border:2px solid var(--green);border-radius:50%;box-sizing:border-box}
  .brand-name{color:var(--teal);font-size:15px;font-weight:300;letter-spacing:.3px}
  .person{position:absolute;left:42px;top:92px}
  .person-name{color:var(--teal);font-size:13px;font-weight:400;margin:0}
  .person-title{color:var(--muted);font-size:6px;margin:3px 0 0}
  .contacts{position:absolute;left:42px;top:128px;margin:0;padding:0;list-style:none}
  .contacts li{display:flex;align-items:center;gap:4px;color:var(--ink);font-size:7.5px;font-weight:300;height:10.3px}
  .contacts svg{width:7px;height:7px;fill:var(--teal)}
</style>
</head>
<body>
  <svg width="0" height="0" style="position:absolute">
    <defs>
      <symbol id="icon-phone" viewBox="0 0 10 10"><path d="M1 3.5C1 2 3 1 5 1s4 1 4 2.5L7.5 4 7 3H3l-.5 1zM2.5 5h5l1 4h-7z"/></symbol>
      <symbol id="icon-mobile" viewBox="0 0 10 10"><path d="M2.5 0h5a1 1 0 0 1 1 1v8a1 1 0 0 1-1 1h-5a1 1 0 0 1-1-1V1a1 1 0 0 1 1-1zM3 1.5v6h4v-6z"/></symbol>
      <symbol id="icon-web" viewBox="0 0 10 10"><path d="M5 0a5 5 0 1 0 0 10A5 5 0 0 0 5 0zm0 1c.6.7 1 2 1.1 3.5H3.9C4 3 4.4 1.7 5 1zM1 5.5h2c0 1.3.3 2.4.8 3.2A4 4 0 0 1 1 5.5zm0-1a4 4 0 0 1 2.8-3.2C3.3 2.1 3 3.2 3 4.5zm3.9 1h2.2C7 7 6.6 8.3 5 9 4.4 8.3 4 7 3.9 5.5zM6.2 8.7c.5-.8.8-1.9.8-3.2h2a4 4 0 0 1-2.8 3.2zM7 4.5c0-1.3-.3-2.4-.8-3.2A4 4 0 0 1 9 4.5z"/></symbol>
    </defs>
  </svg>

  <section class="card card--front" style="left:133px;top:106px">
    <div class="front-name">corvia therapeutics</div>
    <div class="front-address">118 N Maple Avenue Dayton, OH 45402</div>
  </section>

  <section class="card" style="left:458px;top:106px">
    <div class="stripe"></div>
    <div class="brand"><span class="brand-dot"></span><span class="brand-name">corvia therapeutics</span></div>
    <div class="person"><p class="person-name">Martin Hale</p><p class="person-title">President &amp; CEO</p></div>
    <ul class="contacts">
      <li><svg><use href="#icon-phone"/></svg>(800) 555-0140 x210</li>
      <li><svg><use href="#icon-mobile"/></svg>(555) 301-4417</li>
      <li><svg><use href="#icon-web"/></svg>mhale@corviarx.com</li>
    </ul>
  </section>

  <section class="card" style="left:780px;top:106px">
    <div class="stripe"></div>
    <div class="brand"><span class="brand-dot"></span><span class="brand-name">corvia therapeutics</span></div>
    <div class="person"><p class="person-name">Owen Pratt</p><p class="person-title">Chief Financial Officer</p></div>
    <ul class="contacts">
      <li><svg><use href="#icon-phone"/></svg>(800) 555-0140 x235</li>
      <li><svg><use href="#icon-mobile"/></svg>(555) 728-1093</li>
      <li><svg><use href="#icon-web"/></svg>opratt@corviarx.com</li>
    </ul>
  </section>

  <section class="card" style="left:133px;top:306px">
    <div class="stripe"></div>
    <div class="brand"><span class="brand-dot"></span><span class="brand-name">corvia therapeutics</span></div>
    <div class="person"><p class="person-name">Daniel Kerr</p><p class="person-title">Senior Director of Marketing</p></div>
    <ul class="contacts">
      <li><svg><use href="#icon-phone"/></svg>555-214-6630</li>
      <li><svg><use href="#icon-mobile"/></svg>555-862-0457</li>
      <li><svg><use href="#icon-web"/></svg>dkerr@corviarx.com</li>
    </ul>
  </section>

  <section class="card" style="left:458px;top:306px">
    <div class="stripe"></div>
    <div class="brand"><span class="brand-dot"></span><span class="brand-name">corvia therapeutics</span></div>
    <div class="person" style="top:104px"><p class="person-name">Lucas Reed</p></div>
    <ul class="contacts">
      <li><svg><use href="#icon-phone"/></svg>(800) 555-0140 x247</li>
      <li><svg><use href="#icon-mobile"/></svg>(555) 419-2286</li>
      <li><svg><use href="#icon-web"/></svg>lreed@corviarx.com</li>
    </ul>
  </section>

  <section class="card" style="left:780px;top:306px">
    <div class="stripe"></div>
    <div class="brand"><span class="brand-dot"></span><span class="brand-name">corvia therapeutics</span></div>
    <div class="person"><p class="person-name">Henry Lowe</p><p class="person-title">Chief Operations Officer</p></div>
    <ul class="contacts">
      <li><svg><use href="#icon-phone"/></svg>(800) 555-0140 x262</li>
      <li><svg><use href="#icon-mobile"/></svg>(555) 673-5508</li>
      <li><svg><use href="#icon-web"/></svg>hlowe@corviarx.com</li>
    </ul>
  </section>
</body>
</html>
```